first fantastic look and impression

We are looking for a concept for letterhead, business card, emailfooter and template for invoices or offers for our company in the consultation business.
The dancer is a symbol who we are: it looks simple, but there is a lot of hard work and many years of training in this movement. The look is also what we want: elegant, modern, strong, with a touch of extravaganza
Target Market(s)
Hotelbusiness , Consulting
Font styles to use
Sans Serif
Other font styles liked:
- please give us a option we are open
Requirements
Must have
- We are not typical consultants but sparring partners and coaches for the hotel and that should also be expressed in the design. Maybe there is an icon that supports the whole thing. We are more modern and bolder than our industry colleagues.
we are modern, fresh, agile, fast
Nice to have
- a icon

```html
<!DOCTYPE html>
<html lang="en">
<head>
<meta charset="utf-8">
<title>Halvorsen+Partner – Letterhead</title>
<link rel="stylesheet" href="https://fonts.googleapis.com/css2?family=Open+Sans:wght@400;700&display=swap">
<style>
  :root {
    --backdrop: #d7dcdd;
    --paper: #ffffff;
    --steel-blue: #6a8aa8;
    --deep-blue: #3f6489;
    --ink-grey: #5a5f66;
    --gold-light: #f0d9a4;
    --gold-deep: #d9b76e;
    --rule: #b9c4cf;
  }
  html, body {
    margin: 0;
    padding: 0;
    width: 1200px;
    height: 784px;
    overflow: hidden;
    background: var(--backdrop);
  }
  .canvas {
    position: relative;
    width: 1200px;
    height: 784px;
  }
  .letterhead {
    position: absolute;
    left: 338px;
    top: 22px;
    width: 523px;
    height: 740px;
    background: var(--paper);
    box-shadow: 0 6px 22px rgba(60, 70, 80, 0.18);
    overflow: hidden;
  }
  .corner-accent {
    position: absolute;
    inset: 0;
    width: 100%;
    height: 100%;
  }
  .brand {
    position: absolute;
    left: 70px;
    top: 34px;
    display: flex;
    flex-direction: column;
    align-items: center;
    gap: 8px;
  }
  .brand-square {
    width: 52px;
    height: 52px;
    box-sizing: border-box;
    border: 1.5px solid var(--steel-blue);
    background: var(--paper);
  }
  .brand-name {
    margin: 0;
    font-family: "Open Sans", Arial, sans-serif;
    font-weight: 400;
    font-size: 13px;
    letter-spacing: 0.4px;
    color: var(--steel-blue);
    white-space: nowrap;
  }
  .contact {
    position: absolute;
    left: 362px;
    top: 70px;
    margin: 0;
    padding: 0 0 0 14px;
    list-style: none;
    border-left: 1px solid var(--rule);
    font-family: "Open Sans", Arial, sans-serif;
    font-size: 8.5px;
    line-height: 13px;
    color: var(--ink-grey);
  }
  .contact li {
    display: flex;
    align-items: center;
    gap: 5px;
  }
  .contact .location {
    font-weight: 700;
    color: var(--deep-blue);
  }
  .contact-icon {
    width: 8px;
    height: 8px;
    flex: none;
  }
</style>
</head>
<body>
<main class="canvas">
  <section class="letterhead" aria-label="Company letterhead">
    <svg class="corner-accent" viewBox="0 0 523 740" preserveAspectRatio="none" aria-hidden="true">
      <defs>
        <linearGradient id="blue-wedge" x1="0" y1="0" x2="1" y2="1">
          <stop offset="0" stop-color="#6f8fae"/>
          <stop offset="1" stop-color="#9fb4c8"/>
        </linearGradient>
        <linearGradient id="gold-wedge" x1="0" y1="0" x2="1" y2="1">
          <stop offset="0" stop-color="#f0d9a4"/>
          <stop offset="1" stop-color="#d9b76e"/>
        </linearGradient>
      </defs>
      <polygon points="0,0 220,0 0,74" fill="url(#blue-wedge)"/>
      <polygon points="262,740 523,740 523,712" fill="url(#gold-wedge)"/>
    </svg>

    <div class="brand">
      <span class="brand-square" aria-hidden="true"></span>
      <p class="brand-name">Halvorsen+Partner</p>
    </div>

    <ul class="contact">
      <li class="location">
        <svg class="contact-icon" viewBox="0 0 8 8" aria-hidden="true">
          <circle cx="4" cy="4" r="4" fill="var(--steel-blue)"/>
          <path d="M4 1.6a1.5 1.5 0 0 1 1.5 1.5C5.5 4.3 4 6.2 4 6.2S2.5 4.3 2.5 3.1A1.5 1.5 0 0 1 4 1.6z" fill="#fff"/>
        </svg>
        Lindenau/Austria
      </li>
      <li>
        <svg class="contact-icon" viewBox="0 0 8 8" aria-hidden="true">
          <circle cx="4" cy="4" r="4" fill="var(--steel-blue)"/>
          <rect x="2" y="2.7" width="4" height="2.8" fill="none" stroke="#fff" stroke-width="0.6"/>
          <path d="M2 2.8 4 4.3 6 2.8" fill="none" stroke="#fff" stroke-width="0.6"/>
        </svg>
        info@halvorsenpartner.com
      </li>
      <li>
        <svg class="contact-icon" viewBox="0 0 8 8" aria-hidden="true">
          <circle cx="4" cy="4" r="4" fill="var(--steel-blue)"/>
          <circle cx="4" cy="4" r="2" fill="none" stroke="#fff" stroke-width="0.6"/>
          <path d="M2 4h4M4 2v4" stroke="#fff" stroke-width="0.5"/>
        </svg>
        halvorsenpartner.com
      </li>
    </ul>
  </section>
</main>
</body>
</html>
```